Calvanto Group Real Estate Company business cards

New business card design, we are generally happy with the basic layout of the existing front of business card, (feel free to change) but require a head shot photo on the back side.

http://www.calvanto.com.au/

Attached logos, and existing business card

------------------------------

Target Market(s)

Real estate

Industry/Entity Type

Real Estate

Contact Information for Business Card

Standard size double sided

Font styles to use
Other font styles liked:
• Futura

Requirements
Must have
• Photo head shot on the back side
Nice to have
• yes
Should not have
• No

```html
<!DOCTYPE html>
<html lang="en">
<head>
<meta charset="utf-8">
<title>Calvanto Group – Business Card</title>
<link rel="stylesheet" href="https://fonts.googleapis.com/css2?family=Source+Sans+3:wght@400;600;700&display=swap">
<style>
  :root {
    --page-bg: #eeeeec;
    --card-orange: #f39a2b;
    --card-grey: #d6d6d6;
    --brand-navy: #2d2462;
    --text-white: #ffffff;
    --photo-light: #e6e7e9;
    --photo-dark: #3a4256;
  }
  * { box-sizing: border-box; margin: 0; padding: 0; }
  html, body {
    width: 1200px; height: 900px; overflow: hidden;
    background: var(--page-bg);
    font-family: "Source Sans 3", "Myriad Pro", sans-serif;
  }
  .canvas { position: relative; width: 1200px; height: 900px; }

  .card {
    position: absolute;
    box-shadow: 0 6px 18px rgba(0,0,0,0.18);
    overflow: hidden;
  }

  /* Front */
  .card-front {
    left: 238px; top: 62px; width: 555px; height: 342px;
    background: var(--card-orange);
    color: var(--text-white);
  }
  .brand-name {
    position: absolute; right: 34px; top: 36px;
    font-size: 60px; font-weight: 600; letter-spacing: 1px;
    color: var(--brand-navy); line-height: 1;
  }
  .person { position: absolute; left: 31px; top: 118px; }
  .person-name { font-size: 21px; font-weight: 700; line-height: 1.1; }
  .person-role { font-size: 15px; font-weight: 400; margin-top: 3px; }
  .company { position: absolute; left: 32px; top: 176px; }
  .company-name { font-size: 18px; font-weight: 600; }
  .company-abn { font-size: 15px; margin-top: 2px; }
  .company-abn strong { font-weight: 700; }

  .contact-list {
    position: absolute; left: 30px; top: 244px;
    list-style: none; font-size: 15px;
  }
  .contact-list li {
    display: flex; align-items: center; height: 23.5px;
  }
  .contact-list svg { width: 12px; height: 12px; margin-right: 13px; fill: var(--text-white); }

  /* Back */
  .card-back {
    left: 458px; top: 518px; width: 559px; height: 343px;
    background: var(--card-grey);
    color: var(--brand-navy);
  }
  .back-brand {
    position: absolute; left: 32px; top: 78px;
    font-size: 46px; font-weight: 600; letter-spacing: 1px; line-height: 1;
  }
  .tagline {
    position: absolute; left: 32px; top: 219px;
    font-size: 19px; font-weight: 600;
  }
  .services {
    position: absolute; left: 31px; top: 264px;
    font-size: 20px; font-weight: 600; word-spacing: 4px;
  }
  .headshot {
    position: absolute; left: 302px; top: 0; width: 257px; height: 343px;
    background: linear-gradient(180deg, var(--photo-light) 0%, #d9dbdf 45%, var(--photo-dark) 100%);
  }
</style>
</head>
<body>
<main class="canvas">

  <section class="card card-front" aria-label="Business card front">
    <div class="brand-name">calvanto</div>

    <div class="person">
      <p class="person-name">Daniel Tran</p>
      <p class="person-role">Director</p>
    </div>

    <div class="company">
      <p class="company-name">Calvanto Group</p>
      <p class="company-abn"><strong>ABN:</strong> 51 824 753 096</p>
    </div>

    <ul class="contact-list">
      <li>
        <svg viewBox="0 0 24 24" aria-hidden="true"><path d="M6.6 10.8a15.1 15.1 0 0 0 6.6 6.6l2.2-2.2c.3-.3.7-.4 1-.2 1.1.4 2.3.6 3.6.6.6 0 1 .4 1 1V20c0 .6-.4 1-1 1C10.6 21 3 13.4 3 4c0-.6.4-1 1-1h3.5c.6 0 1 .4 1 1 0 1.3.2 2.5.6 3.6.1.3 0 .7-.2 1z"/></svg>
        0412 558 306
      </li>
      <li>
        <svg viewBox="0 0 24 24" aria-hidden="true"><path d="M2 5h20v14H2z M2 5l10 8 10-8" fill="none" stroke="#fff" stroke-width="0"/><path d="M2 5h20v2l-10 7L2 7z M2 9l10 7 10-7v10H2z"/></svg>
        daniel.tran@calvanto.com.au
      </li>
      <li>
        <svg viewBox="0 0 24 24" aria-hidden="true"><circle cx="12" cy="12" r="10"/><path d="M2 12h20M12 2c3 3 3 17 0 20M12 2c-3 3-3 17 0 20" stroke="#f39a2b" stroke-width="1.6" fill="none"/></svg>
        www.calvanto.com.au
      </li>
    </ul>
  </section>

  <section class="card card-back" aria-label="Business card back">
    <div class="back-brand">calvanto</div>
    <p class="tagline">let us show you property</p>
    <p class="services">Buy - Sell - Rent</p>
    <div class="headshot" role="img" aria-label="Head shot photo of the director in a navy suit and blue tie against a light grey wall"></div>
  </section>

</main>
</body>
</html>
```